MRT Property - Business Cards

Looking for a business card & general letterhead, signage etc design for our new logo.

Colours:
000a20
0056a2
00b5ef
0088ce
68cef2

Fonts:
Poppins
Karla

Please keep look and feel of new brand - example in the zip package I sent.

```html
<!DOCTYPE html>
<html lang="en">
<head>
<meta charset="utf-8">
<title>MRT Property – Business Cards</title>
<link rel="stylesheet" href="https://fonts.googleapis.com/css2?family=Poppins:wght@400;500;600;700&display=swap">
<style>
  :root {
    --ink: #000a20;
    --navy: #0056a2;
    --sky: #00b5ef;
    --mid: #0088ce;
    --pale: #68cef2;
    --name-blue: #29a8e0;
    --rule: #2a5fa0;
    --grey-text: #333a44;
    --card-back: #1688cc;
    --back-mark: #4fa8df;
    --backdrop: #e8e5e0;
  }
  * { margin: 0; padding: 0; box-sizing: border-box; }
  html, body {
    width: 900px; height: 1200px; overflow: hidden;
    background: var(--backdrop);
    font-family: "Poppins", sans-serif;
  }
  .canvas { position: relative; width: 900px; height: 1200px; }

  .card {
    position: absolute; left: 80px; width: 742px; height: 442px;
    border-radius: 30px; overflow: hidden;
  }
  .card--front { top: 130px; background: #fff; }
  .card--back { top: 638px; background: var(--card-back); }

  .brand {
    position: absolute; right: 40px; top: 60px;
    display: flex; align-items: center; gap: 12px;
  }
  .brand__dot { width: 22px; height: 22px; border-radius: 50%; background: var(--mid); }
  .brand__name {
    font-weight: 600; font-size: 40px; line-height: 1; color: var(--navy);
  }

  .person { position: absolute; left: 37px; top: 276px; }
  .person__name { font-weight: 600; font-size: 27px; line-height: 1.2; color: var(--name-blue); }
  .person__role { font-size: 16px; color: var(--grey-text); line-height: 1.2; }

  .divider {
    position: absolute; left: 37px; right: 33px; top: 336px;
    height: 1.5px; background: var(--rule);
  }

  .contacts {
    position: absolute; left: 37px; top: 348px; list-style: none;
    font-size: 16px; color: var(--grey-text); line-height: 22px;
  }
  .contacts li { display: flex; align-items: center; gap: 11px; }
  .contacts svg { width: 15px; height: 15px; fill: var(--mid); }

  .address {
    position: absolute; left: 475px; top: 368px;
    font-size: 16px; line-height: 20px; color: var(--grey-text);
  }

  .band { position: absolute; left: 0; bottom: 0; width: 742px; height: 16px; }

  .back-mark {
    position: absolute; inset: 0;
    display: flex; align-items: center; justify-content: center; gap: 22px;
  }
  .back-mark__dot { width: 46px; height: 46px; border-radius: 50%; background: var(--back-mark); }
  .back-mark__name {
    font-weight: 600; font-size: 76px; line-height: 1; color: var(--back-mark);
  }
</style>
</head>
<body>
<main class="canvas">
  <section class="card card--front">
    <div class="brand">
      <span class="brand__dot"></span>
      <span class="brand__name">MRT Property</span>
    </div>

    <div class="person">
      <p class="person__name">Dana Whitfield</p>
      <p class="person__role">Owner</p>
    </div>

    <div class="divider"></div>

    <ul class="contacts">
      <li>
        <svg viewBox="0 0 16 16"><path d="M3 2h3l1.5 3.5-2 1.2a8 8 0 0 0 3.8 3.8l1.2-2L14 10v3a1 1 0 0 1-1 1A11 11 0 0 1 2 3a1 1 0 0 1 1-1z"/></svg>
        215-555-0142
      </li>
      <li>
        <svg viewBox="0 0 16 16"><path d="M1 3h14v1.2L8 9 1 4.2z"/><path d="M1 5.8l7 4.8 7-4.8V13H1z"/></svg>
        info@mrtproperty.com.au
      </li>
      <li>
        <svg viewBox="0 0 16 16"><circle cx="8" cy="8" r="7"/></svg>
        www.mrtproperty.com.au
      </li>
    </ul>

    <p class="address">48 Harbor View Road, Suite 210<br>Milford, PA 18337</p>

    <svg class="band" viewBox="0 0 742 16" preserveAspectRatio="none">
      <rect x="0" y="0" width="742" height="16" fill="var(--pale)"/>
      <polygon points="0,0 478,0 462,16 0,16" fill="var(--mid)"/>
      <polygon points="470,0 482,0 466,16 454,16" fill="#ffffff"/>
    </svg>
  </section>

  <section class="card card--back">
    <div class="back-mark">
      <span class="back-mark__dot"></span>
      <span class="back-mark__name">MRT Property</span>
    </div>
  </section>
</main>
</body>
</html>
```